Corvane Business Cards

Front of business card will have logo, name, address, & telephone number. Back of card will have a list of services provided - Roads, Substation Pads, Temporary Pads, Site Pads, Land Leveling, Powerline Row Cleaning, Land Clearing, Gates, Fencing, Construction Entrances, Excavation, Trenching, Underground Utilities, Directional Boring, Pile Driving. We are a construction company that uses heavy equipment like bulldozers, motor graders/blades, dump trucks, backhoes, hydro axes, & skid loaders. We build roads, pads, & install electric utility lines & waterlines underground. This logo is new. The word "Construction" can be smaller as uploaded 2 example edited logos. We will be using this card design for many employees.
Target Market(s)
Industrial Electric Powerline, Wind Turbine, Solar Panel, & Water Utility companies.
Contact Information for Business Card
Name/Position - Dwayne Halster - Owner
Address: 4875 FM 309
Harlow Springs, TX 79412
Phone number - (325) 482-5096

```html
<!DOCTYPE html>
<html lang="en">
<head>
<meta charset="UTF-8">
<title>Corvane Construction – Business Cards</title>
<link href="https://fonts.googleapis.com/css2?family=Poppins:wght@400;600&display=swap" rel="stylesheet">
<style>
  :root {
    --bg: #9a9a9a;
    --maroon: #3f0f1b;
    --maroon-text: #4a1420;
    --silver: #d6d6d6;
    --paper: #ffffff;
    --ink: #4a4a4a;
    --line: #6b2a36;
  }
  * { margin: 0; padding: 0; box-sizing: border-box; }
  html, body { width: 1200px; height: 960px; overflow: hidden; }
  body {
    background: var(--bg);
    font-family: "Poppins", sans-serif;
    position: relative;
  }
  .card {
    position: absolute;
    width: 560px;
    height: 320px;
    box-shadow: 0 10px 24px rgba(0,0,0,0.28);
  }
  .card-back {
    left: 70px; top: 110px;
    background: var(--maroon);
    color: var(--paper);
    display: flex; flex-direction: column; align-items: center; justify-content: center;
  }
  .card-front {
    left: 570px; top: 520px;
    background: var(--paper);
    display: flex; align-items: center;
  }
  .wordmark {
    display: flex; align-items: center; gap: 12px;
    font-weight: 600; letter-spacing: 2px; line-height: 1.1;
  }
  .wordmark-dot { width: 14px; height: 14px; border-radius: 50%; flex: none; }
  .wordmark-text { display: flex; flex-direction: column; }
  .wordmark-name { font-size: 40px; }
  .wordmark-sub { font-size: 17px; letter-spacing: 3px; }
  .card-back .wordmark { color: var(--silver); }
  .card-back .wordmark-dot { background: var(--silver); }
  .services {
    margin-top: 40px;
    font-size: 12px; line-height: 1.45;
    text-align: center; color: var(--paper);
  }
  .front-logo { width: 280px; display: flex; justify-content: center; }
  .card-front .wordmark { color: var(--maroon-text); }
  .card-front .wordmark-name { font-size: 32px; }
  .card-front .wordmark-sub { font-size: 14px; }
  .card-front .wordmark-dot { background: var(--maroon-text); }
  .divider { width: 1px; height: 150px; background: var(--line); flex: none; }
  .contact { padding-left: 24px; padding-right: 16px; color: var(--ink); font-size: 13px; line-height: 1.35; }
  .contact-name { color: var(--maroon-text); font-weight: 600; font-size: 17px; letter-spacing: 0.5px; }
  .contact-role { margin-bottom: 10px; }
  .contact-address { margin-bottom: 10px; }
  .contact-row { display: flex; align-items: center; gap: 8px; white-space: nowrap; }
  .contact-row svg { width: 11px; height: 11px; fill: var(--maroon-text); flex: none; }
</style>
</head>
<body>
  <section class="card card-back" aria-label="Card back">
    <div class="wordmark">
      <span class="wordmark-dot"></span>
      <div class="wordmark-text">
        <span class="wordmark-name">CORVANE</span>
        <span class="wordmark-sub">CONSTRUCTION</span>
      </div>
    </div>
    <p class="services">
      Roads • Substation Pads • Temporary Pads • Site Pads • Land Leveling<br>
      Powerline Row Cleaning • Land Clearing • Gates • Fencing • Construction Entrances<br>
      Excavation • Trenching • Underground Utilities • Directional Boring • Pile Driving
    </p>
  </section>

  <section class="card card-front" aria-label="Card front">
    <div class="front-logo">
      <div class="wordmark">
        <span class="wordmark-dot"></span>
        <div class="wordmark-text">
          <span class="wordmark-name">CORVANE</span>
          <span class="wordmark-sub">CONSTRUCTION</span>
        </div>
      </div>
    </div>
    <div class="divider"></div>
    <div class="contact">
      <p class="contact-name">DWAYNE HALSTER</p>
      <p class="contact-role">Owner</p>
      <p class="contact-address">4875 FM 309<br>Harlow Springs, TX 79412</p>
      <p class="contact-row">
        <svg viewBox="0 0 24 24"><path d="M6.6 10.8a15.1 15.1 0 0 0 6.6 6.6l2.2-2.2c.3-.3.7-.4 1-.2 1.1.4 2.3.6 3.6.6.6 0 1 .4 1 1V20c0 .6-.4 1-1 1A17 17 0 0 1 3 4c0-.6.4-1 1-1h3.5c.6 0 1 .4 1 1 0 1.3.2 2.5.6 3.6.1.3 0 .7-.2 1z"/></svg>
        (325) 482-5096
      </p>
      <p class="contact-row">
        <svg viewBox="0 0 24 24"><path d="M2 5h20v14H2z M2 5l10 8 10-8" fill="none" stroke="#4a1420" stroke-width="2.4"/></svg>
        info@corvaneconstruction.com
      </p>
      <p class="contact-row">
        <svg viewBox="0 0 24 24"><circle cx="12" cy="12" r="10" fill="none" stroke="#4a1420" stroke-width="2.4"/><path d="M2 12h20M12 2c3 3 3 17 0 20M12 2c-3 3-3 17 0 20" fill="none" stroke="#4a1420" stroke-width="1.8"/></svg>
        www.corvaneconstruction.com
      </p>
    </div>
  </section>
</body>
</html>
```